Website front end design for an education nonprofit

This project involves design and development of the website front end (i.e., Web user interface and user experience design) for TAVO Sphere, a nonprofit initiative for developing an online platform for basic English language instruction, especially targeted toward underprivileged, non-native English speaking populations.

More about us: We are a team of educators, researchers and engineers passionate about this cause and would like to invite talented, creative web developers to join us in this effort to create positive social impact! Please send a personal message to the project owner for the executive summary to get more information about our initiative, big picture vision and the team.

TAVO Sphere website front end (UI/UX) design
Our key goals for this project are to develop an impressive Drupal-based front end for our website as well as to find really talented and creative web/UI/UX designers-cum-developers who are experts in the state-of-the-art web technologies, and are passionate about the cause of global online basic education. At the end of this project, we hope to have long term engagement with the selected developer(s) for our future website design and development needs.

Here are some preliminary guidelines on the TAVO Sphere website front end framework as envisioned by us so far. Please note that we would very much encourage creative ideas and mock-ups from the developers.

1. Current platform: Our website prototype back-end uses Drupal CMS (we plan to continue using Drupal CMS) and at the moment, a toy front-end is based on the Drupal Skeleton platform for its simplicity, clean UI and mobile device friendliness. The web developer / designer can choose any Drupal front end as a starting point or come up with a new Drupal template that meets our requirements below. Prior experience and expertise on Drupal would be great.

2. Audience profile: While the primary audience for the website is expected to be young kids (6-10 years) not very familiar with English, the secondary audience also includes adults interested in basic English language skills. So the overall goal is to have simple, uncluttered / clean, elegant and lightweight (think loading time as well as mobile device friendliness) interface that is extremely intuitive and easy to navigate, is artistic and aesthetically appealing to a wide audience (especially the non-native English speaking populations). The most important point is that our target audience should feel welcome with the clean, crisp look and easy, user-centric navigation, and should in no case feel overwhelmed (say with too much text or clutter on the front page).

3. Front page: Here is a currently envisioned preliminary sketch of the website front page (very much open for refinement and improvements)
a. The top “menu bar” part of the landing page will have our organization name and logo along with (or above) the top menu bar with the following links and sub-links
i. “Learn” link with sub-menu of all our content sections (World learning, Basic sentence learning, Classic short stories, Picture Dictionary)
ii. “About” links with information about us (sub-menu entries: About TAVO Sphere, Team, Supporters, Contributors)
iii. “Contribute” link with sub-menu entries Donate, Volunteer
iv. Menu entries towards the right side: “Login / sign up” followed by
v. “Search” with space to enter the search phrase
b. The middle “main page content” part of the page is where we would have entry points to our main content categories. The portion is envisioned to be graphical, with big blocks (images) as links to our content categories. The current categories (to start with) include 1. Word learning, 2. Basic sentence learning, and 3. Classic stories. We welcome creative ideas to represent these content categories in an appealing and elegant way (for example, these content categories could be portrayed as closed double doors that lead to the pages with the content. We would like to have placeholders for appropriate image links to different content categories – we should be able to put appropriate images or change them as we come up with new ideas that would work best with our target audience). The categories would change and grow as our content evolves, hence the core idea is to build a flexible framework that readily allows for expansion as well as customization.
c. The bottom menu / links bar portion of the landing page will have a list of links that are not included at the top. Examples include (with flexibility needed to add more when needed)
i. “Help”: this leads to a new page with FAQ, How to use
ii. “Contact us” link to a web contact form page
iii. “For Teachers” link to a page with information such as how to use, tips, pilot programs,
iv. “Volunteer” link to page with links such as Donate, Volunteer
v. “Contributors” that would link to a page with information about our Artists, Teachers, Writers, Developers etc.
vi. “Jobs” would link to a jobs page
vii. “Blog” would lead to our blog page
viii. “User stories” link to pages with feedback that we obtain from the users about how the content has helped them,
ix. Web 2.0 placeholders for social media (to be added later)

d. The footer of the website should include text “2013 TAVO Sphere, All rights reserved.”

4. The middle block of the front page is the largest in screen real estate and perhaps the most challenging part that requires much creativity and thought on the UI/UX design aspect – the content pages pointed to by the section links on the middle portion of the front page are also being designed.

5. Color preference is towards soft, elegant (think grays, whites, light blues, other light colors) web safe colors. No harsh (too bright, garish) colors.

6. Fonts preference Nice, clean looking fonts (Arial alright) compatible across browsers.

7. Portability and robustness of the front page layout for different platforms should be carefully considered. Although our first launch target platform is PC (where cross browser compatibility is important), this would very soon be followed by mobile devices such as tablets and smartphones given their prevalence across the globe. This mobile friendly design or easy portability to mobile platforms with little work requirement should be considered as a design requirement.

8. Front page as a framework for the complete website: Note that the top and the bottom portions of the front page are envisioned be used as a common template / frame across all the pages of our website – the middle portion would be used to show our content on the other pages of our website.

9. UX: For the UI/UX design, it is critical to keep in mind key qualities such as ease of use, simplicity, elegance and artistic appeal. Some specific points to keep in mind: (1) the major portion of the target audience would be new to English and (2) young children are expected to be the primary audience but we want the website to appeal to adults interested in learning as well, and (3) we need the website to work even with relatively slow Internet speeds (for underdeveloped / developing regions especially), should always be kept in mind. HTML5 compliance ideas are encouraged.

10. Strictly not desired: Typical corporate feel seen in many webpages, blocky graphics, dull and uninviting overall look with no personality, Flash type effects, harsh colors.

11. Creativity and imagination necessary: We would like to reiterate that the designer/developer has complete freedom to re-imagine the front page considering the above requirements and get back with ideas for an inspiring layout that presents the content outlined above in an intuitive format, carefully considering our target audience.

A note: As a rule, we will always make sure that our developers and artists get proper credit for their work and are recognized and acknowledged by everyone visiting our website.

Expected deliverables:
Website design psd files AND coded webpage / Drupal template: the corresponding source code and all the required libraries, images etc would be required with minimal documentation / pointers on how to make changes and customizations.

Interested developers are encouraged to first send us preliminary prototype Design for the front page to get feedback on whether their approach and style is in line with our needs and preferences. We will suggest the developers to proceed further if the team thinks there is some potential for a match (of course, the final determination would be from the pool of shortlisted submissions) – otherwise, in case the team does not see potential for a match with our needs or if we have already received multiple submissions that are comparatively more closely aligned with our vision for the website, we'd prefer to be respectful of the developers’ time and effort by requesting them not to proceed further.

Please consider this effort as your contribution to an important social cause of global and accessible online education and not a commercial enterprise (our passion for making a positive impact is what is driving the TAVO Sphere nonprofit team to undertake this initiative!). We would like to invite you to join us in this effort!

Project Deadline Extended
Reason: Due to requests from interested designers, we are extending the deadline. Looking forward to receiving many other creative designs!

Please see the project brief.

Real Estate

• Please see the project brief.

```html
<!DOCTYPE html>
<html lang="en">
<head>
<meta charset="utf-8">
<title>TAVO Sphere – Learn English</title>
<link rel="stylesheet" href="https://fonts.googleapis.com/css2?family=PT+Sans:wght@400;700&display=swap">
<style>
:root{
  --header-dark:#262626;
  --header-dark-2:#333;
  --page-bg:#e9eef0;
  --panel:#ffffff;
  --accent:#4aaed0;
  --accent-dark:#2f8fb3;
  --nav-top:#8fd0e6;
  --nav-bottom:#3f9fc6;
  --text:#4d4d4d;
  --text-dark:#2b2b2b;
  --muted:#777;
  --rule:#d9d9d9;
  --card:#f6f6f6;
  --footer:#2a2a2a;
  --footer-text:#e6e6e6;
}
*{box-sizing:border-box;margin:0;padding:0}
html,body{width:952px;height:1200px;overflow:hidden}
body{
  position:relative;
  font-family:"PT Sans",Arial,sans-serif;
  color:var(--text);
  background:linear-gradient(to bottom,var(--page-bg) 128px,#f2f5f6 1148px);
}
.abs{position:absolute}
.site-header{left:0;top:0;width:952px;height:128px;background:linear-gradient(to bottom,var(--header-dark-2),var(--header-dark))}
.brand{left:73px;top:14px;font-size:42px;font-weight:700;color:#9ddcf2;letter-spacing:.5px;line-height:50px}
.social{top:30px;width:25px;height:25px;background:#e8e8e8;border-radius:2px}
.social.one{left:776px}.social.two{left:816px}.social.three{left:855px}

.frame{left:71px;top:77px;width:809px;height:811px;background:var(--panel)}

.main-nav{left:79px;top:84px;width:794px;height:38px;border-radius:2px;
  background:linear-gradient(to bottom,var(--nav-top),var(--nav-bottom));border:1px solid #3a92b6}
.nav-item{top:0;height:36px;line-height:36px;text-align:center;color:#fff;font-size:13px;font-weight:700;border-right:1px solid rgba(255,255,255,.35)}
.nav-item.active{background:linear-gradient(to bottom,#5bb6d8,#2b86ac)}
.search{left:391px;top:4px;width:263px;height:28px;background:#fff;border-radius:2px}
.search span{position:absolute;left:13px;top:6px;font-size:11.5px;color:#888}
.search-btn{position:absolute;right:4px;top:4px;width:21px;height:20px;background:#8c8c8c;border-radius:2px}
.btn-light{top:5px;height:26px;line-height:24px;background:linear-gradient(#f5f5f5,#dadada);border:1px solid #b8b8b8;border-radius:2px;font-size:11.5px;color:#333;text-align:center;font-weight:700}

.hero{left:79px;top:129px;width:794px;height:273px;background:#eceff1;border:1px solid #dedede}
.hero-inner{left:7px;top:7px;width:780px;height:258px;background:linear-gradient(120deg,#f4f6f8 0%,#e6ebef 55%,#dfe4e8 100%)}
.hero-photo{left:380px;top:0;width:400px;height:258px;background:linear-gradient(90deg,rgba(230,235,239,0) 0%,#c9b8a6 35%,#7e8a55 70%,#c7cdd2 100%)}
.hero h1{left:30px;top:40px;font-size:28px;font-weight:700;color:var(--accent);letter-spacing:.3px}
.hero p{left:30px;top:83px;width:332px;font-size:11.6px;line-height:18.2px;text-align:justify}
.cta{left:30px;top:162px;width:133px;height:33px;background:linear-gradient(#4a4a4a,#262626);border-radius:2px;color:#fff;font-size:14px;line-height:33px;padding-left:31px}
.cta i{position:absolute;left:10px;top:10px;width:13px;height:13px;border-radius:50%;background:#666}
.dots{left:30px;top:228px}
.dots b{display:inline-block;width:11px;height:11px;border-radius:50%;background:#8a8a8a;margin-right:9px}
.dots b:first-child{background:#333}

h2.section{font-size:16.5px;font-weight:700;color:var(--accent)}
.body-copy{font-size:11.6px;line-height:18.2px;text-align:justify}
.video{left:358px;top:456px;width:246px;height:134px;background:#444;padding:4px}
.video .still{width:238px;height:126px;background:linear-gradient(90deg,#4d6a35,#a78b86 45%,#5e7a3c)}
.play{left:96px;top:42px;width:50px;height:50px;border:3px solid #fff;border-radius:50%}
.rule{left:81px;top:613px;width:523px;height:1px;background:var(--rule)}
.more{color:var(--accent-dark)}

.card{top:722px;width:254px;height:146px;background:var(--card);border:1px solid #e0e0e0;padding:12px 14px}
.card h3{font-size:14.2px;font-weight:400;color:var(--text-dark);margin-bottom:9px}
.card p{font-size:11.6px;line-height:18.2px;text-align:justify}
.card .link{display:block;margin-top:8px;font-size:10.5px;font-weight:700;color:#222}

.tile{left:621px;width:253px;border:3px solid #cfcfcf}
.teachers{top:420px;height:117px;background:linear-gradient(90deg,#31473a,#4b6b55 55%,#5d7a69)}
.teachers .pic{right:0;top:0;width:115px;height:111px;background:linear-gradient(#3f5c47,#7a9bb6)}
.tile-title{font-size:19px;font-weight:700;line-height:21px}
.help{top:545px;height:80px;background:#fff}
.stories{top:636px;height:233px;background:#fff}
.stories .pic{left:90px;top:100px;width:155px;height:127px;background:linear-gradient(135deg,#f1e9e5,#d6a59a 45%,#bac8d7)}

.footer-links{left:74px;top:900px;width:820px}
.col{position:absolute;width:215px}
.col h4{font-size:14.5px;font-weight:400;color:#444;margin-bottom:6px}
.col li{list-style:none;font-size:10.7px;line-height:19.9px;color:#555;padding-left:8px;position:relative}
.col li:before{content:"";position:absolute;left:0;top:9px;width:2px;height:2px;background:#777}
.site-footer{left:0;top:1148px;width:952px;height:52px;background:var(--footer);color:var(--footer-text);font-size:11.8px;text-align:center;line-height:52px}
</style>
</head>
<body>
<header class="site-header abs">
  <div class="brand abs">TAVO SPHERE</div>
  <span class="social one abs" aria-label="Social link"></span>
  <span class="social two abs" aria-label="Social link"></span>
  <span class="social three abs" aria-label="Social link"></span>
</header>

<div class="frame abs"></div>

<nav class="main-nav abs">
  <a class="nav-item active abs" style="left:0;width:74px">Home</a>
  <a class="nav-item abs" style="left:74px;width:70px">About</a>
  <a class="nav-item abs" style="left:144px;width:69px">Learn</a>
  <a class="nav-item abs" style="left:213px;width:95px">Contribute</a>
  <div class="search abs"><span>Search course...</span><i class="search-btn">
    <svg width="21" height="20" viewBox="0 0 21 20"><circle cx="9.5" cy="9" r="4" fill="none" stroke="#fff" stroke-width="1.6"/><line x1="12.5" y1="12" x2="15.5" y2="15" stroke="#fff" stroke-width="1.8"/></svg></i></div>
  <a class="btn-light abs" style="left:665px;width:65px">REGISTER</a>
  <a class="btn-light abs" style="left:737px;width:50px">LOG IN</a>
</nav>

<section class="hero abs">
  <div class="hero-inner abs">
    <div class="hero-photo abs" role="img" aria-label="Photo of a smiling student using a laptop"></div>
  </div>
  <h1 class="abs">WORD LEARNING</h1>
  <p class="abs">Cras eget elementum tellus, at luctus sem. Phasellus aliquam, metus sit amet sagittis semper, elit nulla varius erat, vel gravida est magna ut dui. Maecenas malesuada fermentum risus ut sodales. Sed vitae placerat erat. Fusce ac scelerisque nunc.</p>
  <a class="cta abs"><i></i>REGISTER NOW</a>
  <div class="dots abs"><b></b><b></b><b></b><b></b></div>
</section>

<h2 class="section abs" style="left:81px;top:419px">Welcome to TAVO Sphere</h2>
<p class="body-copy abs" style="left:81px;top:451px;width:261px">Sed nunc neque, congue ac metus non, pharetra tempus justo. Donec a malesuada tortor, sit amet commodo urna. Nam venenatis risus sed diam dictum scelerisque. Proin tincidunt tincidunt mauris vitae iaculis. Proin at pulvinar lorem. Mauris a orci non diam aliquet sollicitudin. Nulla volutpat eu lectus eget faucibus. Sed porttitor auctor suscipit. Nam lacus elit, vehicula sed pretium vel, suscipit ac dui</p>
<div class="video abs">
  <div class="still" role="img" aria-label="Video still of a student outdoors"></div>
  <div class="play abs"><svg width="44" height="44" viewBox="0 0 44 44"><path d="M17 12 L32 22 L17 32 Z" fill="#fff"/></svg></div>
</div>

<div class="rule abs"></div>
<h2 class="section abs" style="left:81px;top:626px">Courses</h2>
<p class="body-copy abs" style="left:81px;top:656px;width:523px">Cras eget elementum tellus, at luctus sem. Phasellus aliquam, metus sit amet sagittis semper, elit nulla varius erat, vel gravida est magna ut dui. Maecenas malesuada fermentum risus ut sodales. Sed vitae placerat erat. Fusce ac scelerisque nunc. <span class="more">More Courses...</span></p>

<article class="card abs" style="left:81px">
  <h3>Proin asuscipit sem</h3>
  <p>Donec a malesuada tortor, sit amet commodo urna. Nam venenatis risus sed diam dictum scelerisque. Proin tincidunt tincidunt mauris vitae iaculis. Proin at pulvinar lorem.</p>
  <span class="link">VIEW MORE &#9656;</span>
</article>
<article class="card abs" style="left:347px">
  <h3>Proin asuscipit sem</h3>
  <p>Donec a malesuada tortor, sit amet commodo urna. Nam venenatis risus sed diam dictum scelerisque. Proin tincidunt tincidunt mauris vitae iaculis. Proin at pulvinar lorem.</p>
  <span class="link">VIEW MORE &#9656;</span>
</article>

<aside class="tile teachers abs">
  <div class="pic abs" role="img" aria-label="Photo of a teacher at a chalkboard"></div>
  <div class="tile-title abs" style="left:13px;top:38px;color:#fff">Our<br>Teachers</div>
  <div class="abs" style="left:13px;top:84px;color:#ddd;font-size:10.5px">VIEW MORE &#9656;</div>
</aside>
<aside class="tile help abs">
  <div class="tile-title abs" style="left:13px;top:19px;color:#333">User Help</div>
  <div class="abs" style="left:13px;top:45px;color:#888;font-size:11px">Maecenas malesuada</div>
  <div class="abs" role="img" aria-label="Illustration of a figure carrying a help key" style="left:160px;top:6px;width:78px;height:64px;background:linear-gradient(#f2f2f2,#cfcfcf);border-radius:6px"></div>
</aside>
<aside class="tile stories abs">
  <p class="abs" style="left:13px;top:14px;width:225px;font-size:11.2px;line-height:18.2px;color:#666;text-align:justify"><b style="color:#777;font-size:15px">&ldquo;</b> Cras eget elementum tellus, at luctus sem. semper, elit nulla varius erat, vel gravida est magna ut rutrum leo sed tempus. <b style="color:#777;font-size:15px">&rdquo;</b></p>
  <div class="abs" style="left:13px;top:86px;font-size:11.2px;font-weight:700;color:#333">Student name, City</div>
  <div class="tile-title abs" style="left:16px;top:134px;color:#444">User<br>stories</div>
  <div class="pic abs" role="img" aria-label="Photo of a student lying with a laptop"></div>
</aside>

<nav class="footer-links abs">
  <div class="col" style="left:0;top:0"><h4>Help</h4><ul><li>Integer lobortis</li><li>Curabitur ac commodo diam</li><li>Phasellus tellus nisl</li><li>Aenean fringilla nascetur ridiculus</li></ul></div>
  <div class="col" style="left:217px;top:0"><h4>Contact us</h4><ul><li>Integer lobortis</li><li>Curabitur ac commodo diam</li><li>Phasellus tellus nisl</li><li>Aenean fringilla nascetur ridiculus</li></ul></div>
  <div class="col" style="left:434px;top:0"><h4>For teachers</h4><ul><li>Integer lobortis</li><li>Curabitur ac commodo diam</li><li>Phasellus tellus nisl</li><li>Aenean fringilla nascetur ridiculus</li></ul></div>
  <div class="col" style="left:650px;top:0"><h4>Volunteer</h4><ul><li>Integer lobortis</li><li>Curabitur ac commodo diam</li><li>Phasellus tellus nisl</li><li>Aenean fringilla nascetur ridiculus</li></ul></div>
  <div class="col" style="left:0;top:126px"><h4>Contributors</h4><ul><li>Integer lobortis</li><li>Curabitur ac commodo diam</li><li>Phasellus tellus nisl</li><li>Aenean fringilla nascetur ridiculus</li></ul></div>
  <div class="col" style="left:217px;top:126px"><h4>Jobs</h4><ul><li>Integer lobortis</li><li>Curabitur ac commodo diam</li><li>Phasellus tellus nisl</li><li>Aenean fringilla nascetur ridiculus</li></ul></div>
  <div class="col" style="left:434px;top:126px"><h4>Blog</h4><ul><li>Integer lobortis</li><li>Curabitur ac commodo diam</li><li>Phasellus tellus nisl</li><li>Aenean fringilla nascetur ridiculus</li></ul></div>
  <div class="col" style="left:650px;top:126px"><h4>User stories</h4><ul><li>Integer lobortis</li><li>Curabitur ac commodo diam</li><li>Phasellus tellus nisl</li><li>Aenean fringilla nascetur ridiculus</li></ul></div>
</nav>

<footer class="site-footer abs">Copyright &copy; 2013 &nbsp;TAVO Sphere. &nbsp;All rights reserved.</footer>
</body>
</html>
```